Wordpress 6 pages GLAM design for hair salon

Hi guys.
I need a glam & easy to navigate web design for my (women only) new hair salon.
I have a logo. You can see in attached files.
I like 3d backgrounds.
My favourite colours choice: any variety of pink(hot & very soft), white, black, grey.
I would like to see website very feminine, glamorous & kind of old Hollywood and Dorinda Calloway inspired.
Of course it should have plug ins, like social media, map, security etc.
My website now: http://velmoracoiffure.example

Designs what I like:
http://torvinellastudio.example
http://pelurabeautyloft.example
http://www.quillfernvisualworks.example/boutique-graphic-web-folio.html
Updates

Target Market(s)

WOMEN

Industry/Entity Type

Boutique

Requirements
Should not have
• any cartoon or other characters!

```html
<!DOCTYPE html>
<html lang="en">
<head>
<meta charset="utf-8">
<title>Velmora Coiffure</title>
<link href="https://fonts.googleapis.com/css2?family=Arimo:ital,wght@0,400;0,700;1,400&display=swap" rel="stylesheet">
<style>
:root{
  --pink:#c4386f;
  --pink-deep:#a82659;
  --pink-soft:#e58bb0;
  --pink-pale:#f6d3e1;
  --ink:#222;
  --grey:#777;
  --panel:#f6f6f7;
  --night:#1a1416;
  --white:#fff;
}
*{margin:0;padding:0;box-sizing:border-box}
html,body{width:801px;height:1200px;overflow:hidden}
body{position:relative;background:radial-gradient(ellipse at 50% 30%,#2d2226 0%,var(--night) 70%);font-family:"Arimo",Arial,sans-serif;color:var(--ink)}
.abs{position:absolute}
.header-ornament{left:180px;top:8px;width:440px;height:150px;background:radial-gradient(ellipse at 50% 60%,rgba(196,56,111,.35),rgba(40,30,34,0) 70%)}
.nav{left:78px;top:162px;width:644px;height:36px;background:linear-gradient(#d9588c,var(--pink) 60%,var(--pink-deep));border-radius:3px;box-shadow:0 2px 4px rgba(0,0,0,.5)}
.nav a{position:absolute;top:11px;color:var(--white);font-size:10.5px;text-decoration:none}
.header-plate{left:252px;top:78px;width:284px;height:130px;border-radius:60px;background:linear-gradient(#d9588c,var(--pink) 55%,var(--pink-deep));box-shadow:0 2px 6px rgba(0,0,0,.5)}
.brand{left:252px;top:108px;width:284px;text-align:center;color:var(--white);font-size:31px;font-weight:700;letter-spacing:1px;line-height:34px}
.page{left:88px;top:206px;width:625px;height:944px;background:var(--panel)}
.hero{left:94px;top:216px;width:613px;height:206px;background:linear-gradient(100deg,#2f5a2c 0%,#f1e7b0 25%,#e9c2a6 55%,#6b3b2a 80%,#c4386f 100%)}
.hero-band{left:88px;top:206px;width:625px;height:230px}
.hero-caption{left:167px;top:412px;color:var(--white);font-size:12.5px}
.hero-arrow{width:24px;height:24px;border-radius:50%;background:var(--pink-deep);color:var(--white);font-size:14px;font-weight:700;text-align:center;line-height:23px;top:380px}
.photo{background:linear-gradient(135deg,#e8d2c4,#8a5a44)}
.welcome-photo{left:101px;top:445px;width:154px;height:154px;border-radius:50%;border:2px solid #ddd;background:radial-gradient(circle at 50% 40%,#f2d7c7,#6b4233 75%)}
.welcome-title{left:265px;top:444px;font-size:19px;font-style:italic;color:var(--pink)}
.welcome-text{left:267px;top:478px;width:437px;font-size:8.5px;line-height:19px;color:var(--grey)}
.btn{background:var(--pink);color:var(--white);font-size:8.5px;text-align:center;border-radius:2px}
.btn-main{left:266px;top:562px;width:92px;height:23px;line-height:23px}
.section-title{font-size:13px;color:var(--ink)}
.section-rule{height:3px;border-top:1px solid var(--pink-soft);border-bottom:1px solid var(--pink-soft)}
.flourish{color:var(--pink);font-size:10px}
.service-thumb{width:64px;height:64px;border-radius:50%}
.service-text{width:200px;font-size:7.5px;line-height:15px;color:#444}
.more{font-size:7.5px;color:var(--pink)}
.post-img{width:145px;height:102px}
.post-title{left:263px;width:250px;font-size:13.5px;line-height:15.5px;color:#333;text-align:justify}
.post-meta{left:263px;font-size:6.5px;font-style:italic;color:var(--pink-deep)}
.post-body{left:263px;width:250px;font-size:7px;line-height:11.5px;font-style:italic;color:var(--grey);text-align:justify}
.btn-post{left:263px;width:64px;height:13px;line-height:13px}
.hours{left:545px;top:720px;width:156px;height:96px;background:linear-gradient(135deg,#d9588c,var(--pink-soft));border:2px solid #e07aa3}
.hours-photo{left:0;top:8px;width:62px;height:84px;background:linear-gradient(#f3dccf,#f7f3f0)}
.hours h3{position:absolute;left:74px;top:18px;font-size:20px;font-weight:400;color:var(--white)}
.hours p{position:absolute;left:75px;font-size:7px;color:var(--white)}
.cal{left:544px;top:850px;width:157px;height:139px;border:1px solid #ddd;background:var(--white)}
.cal span{position:absolute;width:20px;text-align:center;font-size:8.5px;color:#222}
.cal .head{font-weight:700}
.prod-arrow{width:19px;height:19px;top:1011px;color:var(--white);font-size:12px;font-weight:700;text-align:center;line-height:18px}
.prod{top:1043px;height:81px;width:110px}
.divider{height:1px;background:#ddd}
.footer-text{left:86px;top:1170px;font-size:7.5px;color:var(--white)}
.social{top:1163px}
</style>
</head>
<body>
<div class="abs header-ornament" role="img" aria-label="Ornamental floral crest"></div>
<nav class="abs nav">
  <a style="left:21px" href="#">Home</a>
  <a style="left:75px" href="#">About</a>
  <a style="left:129px" href="#">Services</a>
  <a style="left:475px" href="#">Gallery</a>
  <a style="left:536px" href="#">Blog</a>
  <a style="left:582px" href="#">Contacts</a>
</nav>
<div class="abs header-plate"></div>
<div class="abs brand">VELMORA<br>COIFFURE</div>

<main class="abs page" style="top:210px;height:940px"></main>
<svg class="abs hero-band" style="top:212px" width="625" height="224" viewBox="0 0 625 224">
  <rect x="0" y="0" width="625" height="224" fill="#c4386f"/>
</svg>
<div class="abs hero" role="img" aria-label="Model with a white flower in her hair beside a large frangipani blossom"></div>
<svg class="abs" style="left:94px;top:216px" width="613" height="214" viewBox="0 0 613 214">
  <path d="M0 214 L0 196 Q140 170 330 200 Q520 190 613 60 L613 214 Z" fill="#c4386f"/>
</svg>
<div class="abs hero-caption">Velmora Coiffure designs.........</div>
<div class="abs hero-arrow" style="left:634px">‹</div>
<div class="abs hero-arrow" style="left:668px">›</div>

<div class="abs welcome-photo" role="img" aria-label="Portrait of a woman with dark hair"></div>
<h1 class="abs welcome-title" style="font-weight:400">Welcome To Our Website!</h1>
<p class="abs welcome-text">Our salon is based on the belief that our customers' needs are of the utmost importance. Our team is committed to meeting those needs. As a result, a high percentage of our business is from repeat customers and referrals.<br><span style="display:block;margin-top:15px">We would welcome the opportunity to earn your trust and deliver you the best service in the industry!</span></p>
<div class="abs btn btn-main">Read More</div>

<div class="abs section-title" style="left:100px;top:607px">Hair Extensions <span class="flourish">✿</span></div>
<div class="abs section-rule" style="left:213px;top:615px;width:169px"></div>
<div class="abs service-thumb photo" style="left:106px;top:632px" role="img" aria-label="Woman with long flowing hair extensions"></div>
<p class="abs service-text" style="left:182px;top:641px">Lorem ipsum dolor sit amet, consectetuer adipiscing nonummy nibheuismod tincidunt ut laoreet dolore m aliquam erat volutpat. Ut wisi enim.........</p>
<div class="abs more" style="left:344px;top:688px">Read More</div>

<div class="abs section-title" style="left:409px;top:607px">Brazilian Blowout <span class="flourish">✿</span></div>
<div class="abs section-rule" style="left:535px;top:615px;width:163px"></div>
<div class="abs service-thumb photo" style="left:409px;top:632px" role="img" aria-label="Woman with a red flower and smooth curls"></div>
<p class="abs service-text" style="left:485px;top:641px">Lorem ipsum dolor sit amet, consectetuer adipiscing nonummy nibheuismod tincidunt ut laoreet dolore m aliquam erat volutpat. Ut wisi enim.........</p>
<div class="abs more" style="left:661px;top:688px">Read More</div>

<div class="abs section-title" style="left:100px;top:718px">Recent Posts <span class="flourish">✿</span></div>
<div class="abs section-rule" style="left:201px;top:726px;width:312px"></div>

<div class="abs post-img photo" style="left:100px;top:749px;background:linear-gradient(135deg,#f4f1ef,#7a5443)" role="img" aria-label="Smiling woman with brown hair"></div>
<div class="abs post-title" style="top:746px">In Pompeii, 158 thermopolia with a service counter have been identified</div>
<div class="abs post-meta" style="top:778px">Lorem ipsum&nbsp; Lena Hartwell</div>
<p class="abs post-body" style="top:796px">Italian wine is wine produced in Italy, a country which is home to some of the oldest wine-producing regions in the world. Italy is one of the world's foremost producers</p>
<div class="abs btn btn-post" style="top:838px">Read More</div>

<div class="abs post-img photo" style="left:100px;top:871px;background:linear-gradient(135deg,#f3e6d8,#d9b98f)" role="img" aria-label="Woman with wavy blonde hair"></div>
<div class="abs post-title" style="top:868px">In Pompeii, 158 thermopolia with a service counter have been identified</div>
<div class="abs post-meta" style="top:900px">Lorem ipsum&nbsp; Lena Hartwell</div>
<p class="abs post-body" style="top:918px">Italian wine is wine produced in Italy, a country which is home to some of the oldest wine-producing regions in the world. Italy is one of the world's foremost producers</p>
<div class="abs btn btn-post" style="top:960px">Read More</div>

<div class="abs hours">
  <div class="abs hours-photo" role="img" aria-label="Woman holding a white towel"></div>
  <h3>HOURS</h3>
  <p style="top:47px">10am -7pm : Tues-Sat</p>
  <p style="top:62px">11am -5pm : Sunday</p>
</div>

<div class="abs section-title" style="left:544px;top:826px;font-size:11.5px"><span class="flourish">✿</span> January 2014</div>
<div class="abs section-rule" style="left:630px;top:833px;width:71px"></div>
<div class="abs cal">
  <span class="head" style="left:3px;top:5px">M</span><span class="head" style="left:24px;top:5px">T</span><span class="head" style="left:44px;top:5px">W</span><span class="head" style="left:65px;top:5px">T</span><span class="head" style="left:85px;top:5px">F</span><span class="head" style="left:106px;top:5px">S</span><span class="head" style="left:127px;top:5px">S</span>
  <span style="left:44px;top:30px">1</span><span style="left:65px;top:30px">2</span><span style="left:85px;top:30px">3</span><span style="left:106px;top:30px">4</span><span style="left:127px;top:30px">5</span>
  <span style="left:3px;top:54px;text-decoration:underline">6</span><span style="left:24px;top:54px">7</span><span style="left:44px;top:54px">8</span><span style="left:65px;top:54px">9</span><span style="left:85px;top:54px">10</span><span style="left:106px;top:54px">11</span><span style="left:127px;top:54px">12</span>
  <span style="left:3px;top:77px">13</span><span style="left:24px;top:77px">14</span><span style="left:44px;top:77px">15</span><span style="left:65px;top:77px">16</span><span style="left:85px;top:77px">17</span><span style="left:106px;top:77px">18</span><span style="left:127px;top:77px">19</span>
  <span style="left:3px;top:101px">20</span><span style="left:24px;top:101px">21</span><span style="left:44px;top:101px">22</span><span style="left:65px;top:101px">23</span><span style="left:85px;top:101px">24</span><span style="left:106px;top:101px">25</span><span style="left:127px;top:101px">26</span>
  <span style="left:3px;top:124px">27</span><span style="left:24px;top:124px">28</span><span style="left:44px;top:124px">29</span><span style="left:65px;top:124px">30</span><span style="left:85px;top:124px">31</span>
</div>

<div class="abs divider" style="left:100px;top:1002px;width:601px"></div>
<div class="abs section-title" style="left:100px;top:1012px">Our Retail Products <span class="flourish">✿</span></div>
<div class="abs section-rule" style="left:244px;top:1020px;width:410px"></div>
<div class="abs prod-arrow" style="left:658px;background:#aaa">‹</div>
<div class="abs prod-arrow" style="left:682px;background:var(--pink-deep)">›</div>
<div class="abs prod" style="left:100px;background:linear-gradient(120deg,#2a2550,#d8d4e4)" role="img" aria-label="Woman with skincare bottles"></div>
<div class="abs prod" style="left:222px;background:linear-gradient(120deg,#111,#4a4a4a)" role="img" aria-label="Woman with a hair product tube on black"></div>
<div class="abs prod" style="left:345px;background:linear-gradient(120deg,#e9e4f2,#8a6fb0)" role="img" aria-label="Shampoo bottles"></div>
<div class="abs prod" style="left:468px;background:linear-gradient(120deg,#0d0d0d,#8a1b22)" role="img" aria-label="Dancer in a red dress beside a product tube"></div>
<div class="abs prod" style="left:590px;background:linear-gradient(120deg,#f4f0ea,#f0a81e)" role="img" aria-label="Woman with hair care products on orange"></div>
<div class="abs divider" style="left:100px;top:1138px;width:601px"></div>

<div class="abs footer-text">Velmora Hair Studio © 2014 | Privacy Policy</div>
<svg class="abs social" style="left:584px" width="24" height="24" viewBox="0 0 24 24" aria-label="Share">
  <circle cx="12" cy="12" r="11.5" fill="#3a3033" stroke="#ccc"/>
  <circle cx="15.5" cy="8" r="2" fill="#fff"/><circle cx="15.5" cy="16" r="2" fill="#fff"/><circle cx="8.5" cy="12" r="2" fill="#fff"/>
  <path d="M8.5 12 L15.5 8 M8.5 12 L15.5 16" stroke="#fff" stroke-width="1.2"/>
</svg>
<svg class="abs social" style="left:618px" width="24" height="24" viewBox="0 0 24 24" aria-label="Chat">
  <circle cx="12" cy="12" r="11.5" fill="#3a3033" stroke="#ccc"/>
  <path d="M6.5 8 h11 v7 h-6 l-3 2.5 v-2.5 h-2 z" fill="#fff"/>
</svg>
<svg class="abs social" style="left:654px" width="24" height="24" viewBox="0 0 24 24" aria-label="News">
  <circle cx="12" cy="12" r="11.5" fill="#3a3033" stroke="#ccc"/>
  <rect x="7" y="7" width="10" height="10" rx="1" fill="#fff"/>
  <path d="M9 10 h6 M9 12 h6 M9 14 h4" stroke="#3a3033" stroke-width="1"/>
</svg>
<svg class="abs social" style="left:689px" width="24" height="24" viewBox="0 0 24 24" aria-label="Email">
  <circle cx="12" cy="12" r="11.5" fill="#3a3033" stroke="#ccc"/>
  <rect x="6.5" y="8" width="11" height="8" rx="1" fill="#fff"/>
  <path d="M6.5 8.5 L12 12.5 L17.5 8.5" fill="none" stroke="#3a3033" stroke-width="1"/>
</svg>
</body>
</html>
```